Tolbek cards

I want a simple business card that pops.
Logo on one side.
On side two i want.
"Are you thinking about a new building on your property, or renovating an existing structure? Contact".....
Owners Name: Dale Whitacre
Owners Phone number: 610-555-0187
Address:4076 Copper Ridge RD, Elmford, PA 16890
Committed to Quality, Service, and Integrity

```html
<!DOCTYPE html>
<html lang="en">
<head>
<meta charset="utf-8">
<title>Tolbek Builders LLC – Business Card</title>
<link rel="stylesheet" href="https://fonts.googleapis.com/css2?family=Poppins:wght@400;500;600;700&display=swap">
<style>
  :root {
    --page-bg: #f2f2f2;
    --brown-dark: #3f2c1d;
    --brown-deep: #52341e;
    --brown-light: #a08a70;
    --ink: #1a1a1a;
    --white: #ffffff;
  }
  * { margin: 0; padding: 0; box-sizing: border-box; }
  html, body {
    width: 1200px; height: 960px; overflow: hidden;
    background: var(--page-bg);
    font-family: "Poppins", sans-serif;
  }
  .stage { position: relative; width: 1200px; height: 960px; }
  .card {
    position: absolute; top: 112px;
    width: 420px; height: 735px;
    border-radius: 34px; overflow: hidden;
    box-shadow: 0 14px 34px rgba(0,0,0,0.22);
  }
  .card-front {
    left: 149px;
    background: linear-gradient(90deg, var(--brown-light) 0%, #8a735a 30%, #654a32 55%, var(--brown-deep) 75%, var(--brown-deep) 100%);
  }
  .front-brand {
    position: absolute; left: 50%; top: 50%;
    transform: translate(-50%, -50%) rotate(-90deg);
    display: flex; align-items: center; gap: 22px;
    color: var(--white); font-weight: 700; white-space: nowrap;
  }
  .front-brand .mark { width: 40px; height: 40px; background: var(--white); }
  .front-brand .words { display: flex; flex-direction: column; align-items: center; }
  .front-brand .name { font-size: 68px; line-height: 1; letter-spacing: 2px; }
  .front-brand .suffix { font-size: 24px; line-height: 1; letter-spacing: 1px; margin-top: 6px; }

  .card-back { left: 628px; background: var(--white); }
  .pitch {
    position: absolute; top: 22px; left: 0; right: 0;
    text-align: center; font-size: 18.5px; line-height: 25px;
    color: var(--ink); letter-spacing: 0.4px;
  }
  .back-brand {
    position: absolute; top: 108px; left: 0; right: 0;
    display: flex; flex-direction: column; align-items: center;
    color: var(--brown-dark); font-weight: 700;
  }
  .back-brand .mark {
    width: 80px; height: 80px; border-radius: 50%;
    background: var(--brown-dark); margin-bottom: 14px;
  }
  .back-brand .name { font-size: 54px; line-height: 1; letter-spacing: 1px; }
  .back-brand .suffix { font-size: 18px; line-height: 1; margin-top: 6px; letter-spacing: 1px; }

  .owner {
    position: absolute; top: 478px; left: 0; right: 0; text-align: center;
  }
  .owner-name { font-size: 36px; font-weight: 600; color: var(--brown-dark); line-height: 44px; }
  .owner-role { font-size: 17px; font-weight: 500; color: var(--ink); line-height: 18px; }
  .tagline {
    position: absolute; top: 545px; left: 0; right: 0;
    text-align: center; font-size: 18.5px; line-height: 25px; color: var(--ink);
  }
  .contact-band {
    position: absolute; left: 0; right: 0; bottom: 0; height: 113px;
    background: var(--brown-dark); color: var(--white); text-align: center;
  }
  .contact-icons {
    position: absolute; top: -17px; left: 0; right: 0;
    display: flex; justify-content: center; gap: 10px;
  }
  .icon-badge {
    width: 33px; height: 33px; border-radius: 50%;
    background: var(--brown-dark); border: 2px solid var(--white);
    display: flex; align-items: center; justify-content: center;
  }
  .contact-lines {
    position: absolute; top: 20px; left: 0; right: 0;
    font-size: 18.5px; line-height: 25px; letter-spacing: 0.4px;
  }
</style>
</head>
<body>
<main class="stage">
  <section class="card card-front" aria-label="Card front">
    <div class="front-brand">
      <span class="mark"></span>
      <span class="words">
        <span class="name">TOLBEK</span>
        <span class="suffix">BUILDERS LLC</span>
      </span>
    </div>
  </section>

  <section class="card card-back" aria-label="Card back">
    <p class="pitch">"Are you thinking about a new building<br>on your property, or renovating an<br>existing structure? Contact".....</p>

    <div class="back-brand">
      <span class="mark"></span>
      <span class="name">TOLBEK</span>
      <span class="suffix">BUILDERS LLC</span>
    </div>

    <div class="owner">
      <h1 class="owner-name">Dale Whitacre</h1>
      <p class="owner-role">Owners</p>
    </div>
    <p class="tagline">Committed to Quality,<br>Service, and Integrity</p>

    <div class="contact-band">
      <div class="contact-icons">
        <span class="icon-badge" aria-label="Phone">
          <svg width="16" height="16" viewBox="0 0 24 24" fill="none" stroke="#fff" stroke-width="2" stroke-linecap="round" stroke-linejoin="round"><path d="M22 16.9v3a2 2 0 0 1-2.2 2 19.8 19.8 0 0 1-8.6-3.1 19.5 19.5 0 0 1-6-6A19.8 19.8 0 0 1 2.1 4.2 2 2 0 0 1 4.1 2h3a2 2 0 0 1 2 1.7c.1.9.4 1.8.7 2.7a2 2 0 0 1-.5 2.1L8 9.8a16 16 0 0 0 6 6l1.3-1.3a2 2 0 0 1 2.1-.4c.9.3 1.8.6 2.7.7a2 2 0 0 1 1.7 2z"/></svg>
        </span>
        <span class="icon-badge" aria-label="Location">
          <svg width="16" height="16" viewBox="0 0 24 24" fill="none" stroke="#fff" stroke-width="2" stroke-linecap="round" stroke-linejoin="round"><path d="M12 22s7-6.3 7-12a7 7 0 0 0-14 0c0 5.7 7 12 7 12z"/><circle cx="12" cy="10" r="2.5"/></svg>
        </span>
      </div>
      <p class="contact-lines">610-555-0187<br>4076 Copper Ridge RD, Elmford, PA 16890</p>
    </div>
  </section>
</main>
</body>
</html>
```